2016 new customer flyer for zorvella customers

We need a 2 Sided Flyer Design for our website bargains. This will be sent to every customer who orders from us my site is www.vendrift.example - I want a 2 sided flyer, Promoting products on our clearance page and also advertising our guaranteed next day delivery, All items are in stock with QTY showing, This is the actual stock amount in stock. We need the flyers to attract new customers from zorvella to our site, 1 side of the flyer is to include "thank you for buying from our zorvella site" and also please leave positive feedback - with a big 5STARS image. if there is any problems with your order please contact us on 0861 547 219 6 - or email us - sales@vendrift.example

Target Market(s)

New customers who order from our zorvella site

Font styles to use
Sans Serif

Requirements
Must have
• my site is www.vendrift.example - I want a 2 sided flyer, Promoting products on our clearance page and also advertising our guaranteed next day delivery, All items are in stock with QTY showing, This is the actual stock amount in stock. We need the flyers to attract new customers from zorvella to our site, 1 side of the flyer is to include "thank you for buying from our zorvella site" and also please leave positive feedback - with a big 5STARS image. if there is any problems with your order please contact us on 0861 547 219 6 - or email us - sales@vendrift.example
Nice to have
• I need a flash flyer that is eye catching enough to get those customers visiting our site, We have many items on our website - www.vendrift.example

```html
<!DOCTYPE html>
<html lang="en">
<head>
<meta charset="utf-8">
<title>Vendrift customer flyer</title>
<link rel="stylesheet" href="https://fonts.googleapis.com/css2?family=Oswald:wght@500;700&family=Lato:wght@400;700;900&display=swap">
<style>
:root{
  --stage:#e4e4e4;
  --blue:#2a8ce0;
  --blue-deep:#1466c2;
  --blue-light:#5cb4f2;
  --yellow:#fde23a;
  --band:#f6d12e;
  --dark:#2b2b2b;
  --red:#e3262b;
  --red-deep:#a60f14;
  --white:#ffffff;
  --grey:#555555;
}
*{box-sizing:border-box;margin:0;padding:0}
html,body{width:1200px;height:844px;overflow:hidden;background:var(--stage)}
body{position:relative;font-family:'Lato',Arial,sans-serif}
.flyer{position:absolute;top:53px;width:527px;height:740px;overflow:hidden;
  background:radial-gradient(circle at 50% 45%,var(--blue-light),var(--blue) 45%,var(--blue-deep));
  box-shadow:0 4px 14px rgba(0,0,0,.25)}
.flyer--thanks{left:50px}
.flyer--promo{left:624px}
.photo{position:absolute;left:0;top:0;width:527px}
.wave{position:absolute;left:0;width:527px}
.abs{position:absolute}
.center{left:0;right:0;text-align:center;white-space:nowrap}
.card{left:115px;top:116px;width:296px;height:176px;background:var(--white);text-align:center;
  font-family:'Oswald',Arial,sans-serif;font-weight:700;line-height:1}
.card .l1{font-size:64px;color:#111;margin-top:10px;display:block}
.card .l2{font-size:80px;color:var(--red);display:block}
.logo-box{left:135px;top:340px;width:260px;height:69px;background:var(--white);border-radius:10px;
  display:flex;align-items:center;justify-content:center;gap:10px}
.logo-dot{width:18px;height:18px;border-radius:50%;background:var(--blue-deep)}
.logo-name{font-family:'Lato',Arial,sans-serif;font-weight:900;font-size:38px;color:var(--blue-deep)}
.title{font-family:'Oswald',Arial,sans-serif;font-weight:700;color:var(--yellow);font-size:58px;top:420px;line-height:1}
.subtitle{font-family:'Lato',Arial,sans-serif;font-weight:400;color:var(--white);font-size:42px;top:486px;line-height:1}
.feedback-band{left:0;top:545px;width:527px;height:46px;background:var(--band);
  font-family:'Oswald',Arial,sans-serif;font-weight:500;font-size:28px;color:var(--dark);
  display:flex;align-items:center;justify-content:center;letter-spacing:.5px}
.stars-box{left:135px;top:591px;width:260px;height:66px;background:var(--white);border-radius:0 0 10px 10px;
  display:flex;align-items:center;justify-content:center}
.footer{left:15px;top:682px;width:512px;height:58px;background:var(--dark);border-radius:30px 0 0 0;
  color:var(--white);font-size:12px;line-height:15px;text-align:center;padding-top:6px}
.footer .warn{color:var(--yellow);font-weight:700}
.footer .row{display:flex;align-items:center;justify-content:center;gap:6px}
.icon{width:11px;height:11px;fill:var(--yellow)}
.ribbon{left:186px;top:265px;width:153px;height:160px}
.ribbon-text{left:186px;top:275px;width:153px;text-align:center;color:var(--white);line-height:1}
.ribbon-text .pct{font-family:'Oswald',Arial,sans-serif;font-weight:700;font-size:46px;display:block}
.ribbon-text .disc{font-family:'Oswald',Arial,sans-serif;font-weight:500;font-size:24px;color:var(--yellow);display:block;margin-top:4px}
.ribbon-text .new{font-family:'Lato',Arial,sans-serif;font-weight:700;font-size:16px;display:block;margin-top:6px}
.go{font-family:'Oswald',Arial,sans-serif;font-weight:700;color:var(--yellow);font-size:35px;top:440px;line-height:1}
.coupon{font-family:'Oswald',Arial,sans-serif;font-weight:500;color:var(--white);font-size:20px;top:486px;line-height:1.2}
.stock-btn{left:177px;top:521px;width:173px;height:37px;background:var(--red);border:2px solid var(--white);border-radius:10px;
  color:var(--white);font-family:'Oswald',Arial,sans-serif;font-weight:500;font-size:19px;
  display:flex;align-items:center;justify-content:center}
.note{top:570px;color:var(--white);font-size:11px;font-weight:700}
.brand-strip{left:0;top:595px;width:527px;height:56px;background:var(--white);
  display:grid;grid-template-columns:repeat(6,64px);grid-template-rows:repeat(2,24px);gap:2px 4px;padding:4px 0 0 10px}
.brand{font-family:'Lato',Arial,sans-serif;font-weight:700;font-size:10.5px;color:var(--grey);display:flex;align-items:center;white-space:nowrap}
.boxes{left:436px;top:580px;width:72px;height:156px;background:linear-gradient(#c9a57a,#2f6fbf);border-radius:4px}
.footer--promo{left:0;top:678px;width:527px;height:62px;background:var(--dark);color:var(--white)}
.delivery{left:14px;top:10px;line-height:1}
.delivery .big{font-family:'Lato',Arial,sans-serif;font-weight:900;font-size:20px;color:var(--yellow);display:block}
.delivery .small{font-size:14px;display:block;margin-top:4px}
.truck{left:232px;top:12px;width:62px;height:40px}
.contact{left:338px;top:8px;font-size:13px;line-height:15px}
.contact .row{display:flex;align-items:center;gap:6px}
</style>
</head>
<body>

<section class="flyer flyer--thanks">
  <div class="photo" role="img" aria-label="Photo of a hand holding up a white card" style="height:360px;background:linear-gradient(135deg,#c9d4e2,#e9eef5 55%,#b9c7d8)"></div>
  <div class="abs card"><span class="l1">THANK</span><span class="l2">YOU</span></div>
  <svg class="wave" style="top:300px" width="527" height="80" viewBox="0 0 527 80">
    <path d="M0 60 Q263 -10 527 40 L527 80 L0 80Z" fill="var(--dark)"/>
    <path d="M0 66 Q263 0 527 46 L527 80 L0 80Z" fill="var(--band)"/>
    <path d="M0 72 Q263 10 527 54 L527 80 L0 80Z" fill="var(--white)"/>
    <path d="M0 78 Q263 18 527 62 L527 80 L0 80Z" fill="var(--blue)"/>
  </svg>
  <div class="abs logo-box"><span class="logo-dot"></span><span class="logo-name">Vendrift</span></div>
  <h1 class="abs center title">THANK YOU FOR</h1>
  <p class="abs center subtitle">YOUR PURCHASE</p>
  <div class="abs feedback-band">PLEASE LEAVE POSITIVE FEEDBACK</div>
  <div class="abs stars-box" aria-label="Five stars">
    <svg width="230" height="36" viewBox="0 0 230 36">
      <defs><path id="star" d="M18 1 L22.6 12.6 L35 13.4 L25.4 21.4 L28.6 33.6 L18 26.8 L7.4 33.6 L10.6 21.4 L1 13.4 L13.4 12.6Z" fill="var(--red)"/></defs>
      <use href="#star" x="0"/><use href="#star" x="48"/><use href="#star" x="96"/><use href="#star" x="144"/><use href="#star" x="192"/>
    </svg>
  </div>
  <div class="abs footer">
    <p><span class="warn">if there is any problems with your order please</span> <b>contact us on 0861 547 219 6</b></p>
    <p class="row"><svg class="icon" viewBox="0 0 12 12"><path d="M0 2h12v8H0z"/></svg>sales@vendrift.example</p>
    <p class="row"><svg class="icon" viewBox="0 0 12 12"><circle cx="6" cy="6" r="5.5"/></svg>www.vendrift.example</p>
  </div>
</section>

<section class="flyer flyer--promo">
  <div class="photo" role="img" aria-label="Photo of a smiling courier carrying a parcel beside a yellow delivery van" style="height:300px;background:linear-gradient(120deg,#e3c23a,#d9b642 40%,#3a6fc4 65%,#8fb36b)"></div>
  <svg class="wave" style="top:250px" width="527" height="70" viewBox="0 0 527 70">
    <path d="M0 8 Q263 70 527 10 L527 70 L0 70Z" fill="var(--dark)"/>
    <path d="M0 14 Q263 74 527 16 L527 70 L0 70Z" fill="var(--band)"/>
    <path d="M0 20 Q263 78 527 22 L527 70 L0 70Z" fill="var(--white)"/>
    <path d="M0 26 Q263 82 527 28 L527 70 L0 70Z" fill="var(--blue)"/>
  </svg>
  <svg class="abs ribbon" viewBox="0 0 153 160">
    <defs><linearGradient id="rib" x1="0" y1="0" x2="0" y2="1"><stop offset="0" stop-color="var(--red)"/><stop offset="1" stop-color="var(--red-deep)"/></linearGradient></defs>
    <path d="M0 0 H153 V135 L76.5 160 L0 135Z" fill="url(#rib)"/>
  </svg>
  <div class="abs ribbon-text"><span class="pct">10%</span><span class="disc">DISCOUNT</span><span class="new">ON NEW ORDERS</span></div>
  <h2 class="abs center go">GO TO WWW.VENDRIFT.EXAMPLE</h2>
  <p class="abs center coupon">AND USE THIS COUPON CODE&nbsp; NEWC10 FOR DISCOUNT</p>
  <div class="abs stock-btn">LIVE STOCK FIGURES</div>
  <p class="abs center note">We only sell what we have available for next day delivery.</p>
  <div class="abs brand-strip">
    <span class="brand">Vendrift</span><span class="brand">Lumara</span><span class="brand">Pipwick</span><span class="brand">Orbelle</span><span class="brand">Voltane</span><span class="brand">Herocrest</span>
    <span class="brand">Tonefield</span><span class="brand">Powerleaf</span><span class="brand">Soundmere</span><span class="brand">Mixroam</span><span class="brand">Glacia</span><span class="brand">Nova Realms</span>
  </div>
  <div class="abs boxes" role="img" aria-label="Photo of a courier carrying a tall stack of parcels"></div>
  <div class="abs footer--promo">
    <div class="abs delivery"><span class="big">Next Day Delivery</span><span class="small">on orders placed before 12pm</span></div>
    <svg class="abs truck" viewBox="0 0 62 40" aria-label="Delivery truck">
      <rect x="0" y="4" width="38" height="26" rx="3" fill="var(--blue)"/>
      <path d="M40 12 H52 L60 22 V30 H40Z" fill="var(--blue)"/>
      <circle cx="12" cy="33" r="6" fill="var(--blue)" stroke="var(--dark)" stroke-width="2"/>
      <circle cx="50" cy="33" r="6" fill="var(--blue)" stroke="var(--dark)" stroke-width="2"/>
    </svg>
    <div class="abs contact">
      <p class="row"><svg class="icon" viewBox="0 0 12 12"><path d="M2 0h3l1 3-2 1.5a7 7 0 0 0 3.5 3.5L9 6l3 1v3l-2 2C5 12 0 7 0 2z"/></svg>0861 547 219 6</p>
      <p class="row"><svg class="icon" viewBox="0 0 12 12"><path d="M0 2h12v8H0z"/></svg>sales@vendrift.example</p>
      <p class="row"><svg class="icon" viewBox="0 0 12 12"><circle cx="6" cy="6" r="5.5"/></svg>www.vendrift.example</p>
    </div>
  </div>
</section>

</body>
</html>
```